Outdoor Banners for Shopping Center

I need outdoor banners for a small California Shopping Center (Calloway Pines Plaza). You must include the property logo. Each parking lot pole will have 2 banners -- one on each side of the pole so the design should take that into account. Use bright colors… something that will work well with the logo. Size for each banner is 30"w x 96"h. It should be bold and easy to read (if you include any additional text).

Target Market(s)

Middle class shoppers.

Industry/Entity Type

Graphic Design

Font styles to use
Serif
Sans Serif

Requirements
Must have
• The property logo.

```html
<!DOCTYPE html>
<html lang="en">
<head>
<meta charset="utf-8">
<title>Calloway Pines Plaza – Pole Banners</title>
<link rel="stylesheet" href="https://fonts.googleapis.com/css2?family=Playfair+Display:wght@900&display=swap">
<style>
  :root {
    --canvas-bg: #eef1f4;
    --banner-yellow: #f8e71c;
    --banner-magenta: #e5168a;
    --ink-dark: #111111;
    --ink-light: #ffffff;
    --brand-navy: #1d3f8f;
    --art-pink: #f27cc8;
    --art-violet: #b48ae6;
    --art-orange: #ffc26b;
  }
  * { margin: 0; padding: 0; box-sizing: border-box; }
  html, body {
    width: 1200px;
    height: 732px;
    overflow: hidden;
    background: var(--canvas-bg);
  }
  .banner-set {
    width: 1200px;
    height: 732px;
    display: flex;
    justify-content: center;
    align-items: center;
    gap: 44px;
  }
  .banner {
    width: 206px;
    height: 660px;
    display: flex;
    flex-direction: column;
    align-items: center;
    justify-content: space-between;
    padding: 28px 14px;
    font-family: "Playfair Display", Georgia, serif;
    font-weight: 900;
  }
  .banner--yellow { background: var(--banner-yellow); color: var(--ink-dark); }
  .banner--magenta { background: var(--banner-magenta); color: var(--ink-light); }

  .property-mark {
    display: flex;
    align-items: center;
    justify-content: center;
    gap: 8px;
    height: 96px;
    color: var(--brand-navy);
    font-size: 18px;
    line-height: 1.15;
    text-align: left;
  }
  .banner--magenta .property-mark { color: var(--ink-light); }
  .property-mark__dot {
    flex: none;
    width: 20px;
    height: 20px;
    border-radius: 50%;
    background: currentColor;
  }

  .feature-art {
    width: 100%;
    height: 330px;
    border-radius: 12px;
    background: linear-gradient(160deg, var(--art-pink), var(--art-violet) 50%, var(--art-orange));
  }
  .banner--magenta .feature-art {
    background: linear-gradient(200deg, var(--art-orange), var(--art-pink) 50%, var(--art-violet));
  }

  .tagline {
    height: 96px;
    display: flex;
    flex-direction: column;
    justify-content: center;
    font-size: 25px;
    line-height: 1.2;
    text-align: center;
    white-space: nowrap;
  }
</style>
</head>
<body>
  <main class="banner-set">
    <section class="banner banner--yellow">
      <div class="property-mark">
        <span class="property-mark__dot"></span>
        <span>Calloway<br>Pines Plaza</span>
      </div>
      <div class="feature-art" role="img" aria-label="Area for colourful floral burst artwork in pink, violet and orange"></div>
      <p class="tagline"><span>A Great</span><span>Place to Be!</span></p>
    </section>

    <section class="banner banner--magenta">
      <p class="tagline"><span>A Great</span><span>Place to Be!</span></p>
      <div class="feature-art" role="img" aria-label="Area for colourful floral burst artwork in orange, pink and violet"></div>
      <div class="property-mark">
        <span class="property-mark__dot"></span>
        <span>Calloway<br>Pines Plaza</span>
      </div>
    </section>
  </main>
</body>
</html>
```